Website Design for Chef Wen Chinese Restaurant

Chef Wen is a new Chinese Restaurant. It offers exceptional dining experience with authentic and dynamic dishes created with quality ingredients.

A vivid website theme is required to promote this new restaurant online. Logo, menu, wine list and a few other files are attached for help with designing.

A very rough demo website has been setup and can be accessed via http://www.chefwen.com.au. It is for telling designers what content is shown up on each page (except for homepage). By reading the about us page, designers can get some more info of Chef Wen. However, the layout, theme color, font, etc are not set in stone. Visitors should be able to feel Chef Wen restaurant's authentic Chinese cuisine and high hygiene standard. Home page of the website could be The "Our website is coming soon" description is shown on demo site but do not required to be presented on new design.

Some main pages design should be included: Home (landing page), About us, Menu (Dishes), Winelist, Gallery, Contact us. No HTML and coding required. The output should be well layered psd or png files with acceptable resolution for web use.

A few other website can be referred to are:

http://larkspurasian.com.au/
http://www.river-lamp.com/
http://tamworthy.com.au/
http://harbelrestaurant.com.au/
http://www.quillerestaurant.com.au/
http://www.thekiln.com.au/

Industry/Entity Type

Restaurant

Requirements
Nice to have
• I expect designs of at least these webpages: homepage, menu page and contact us page. If you can provide "about us" page as well, it will probably help you win the competition. well layered psd or png file is my preference.
Should not have
• You don't have to make html/cs/js or any coding. All I need is just art design

```html
<!DOCTYPE html>
<html lang="en">
<head>
<meta charset="utf-8">
<title>Chef Wen Chinese Restaurant</title>
<link rel="stylesheet" href="https://fonts.googleapis.com/css2?family=Arimo:wght@400;700&family=Lora:wght@400&display=swap">
<style>
:root{
  --red:#e8171b;
  --red-band:#d9373a;
  --cream:#fffbcf;
  --nav-grey:#dcdcdc;
  --ink:#333;
  --dark:#222;
  --board:#46494b;
  --wood:#6b2e12;
  --chalk:#fffbc0;
  --white:#fff;
}
*{margin:0;padding:0;box-sizing:border-box}
html,body{width:1073px;height:1200px;overflow:hidden;background:var(--white)}
body{font-family:"Arimo",Arial,sans-serif;color:var(--ink);position:relative}
a{text-decoration:none;color:inherit}

.top-bar{position:absolute;left:0;top:0;width:1073px;height:47px;background:var(--red);border-bottom:2px solid #8f1012}
.reservation{position:absolute;left:78px;top:13px;color:var(--white);font-weight:700;font-size:15px;display:flex;align-items:center;gap:6px}
.social{position:absolute;right:100px;top:5px;display:flex;gap:10px}
.social span{width:38px;height:38px;border-radius:50%;background:var(--white);display:flex;align-items:center;justify-content:center}

.header{position:absolute;left:0;top:49px;width:1073px;height:112px;background:var(--cream);border-bottom:2px solid #333}
.ornament{position:absolute;top:8px;width:210px;height:95px;background:radial-gradient(ellipse at center,#f29a4a 0%,#f7c98c 55%,var(--cream) 80%);border-radius:40px}
.ornament.left{left:160px}.ornament.right{left:666px}
.logo-arch{position:absolute;left:410px;top:8px;width:216px;height:153px;background:var(--cream);border-radius:108px 108px 0 0;border-top:4px solid #f3c9a4;display:flex;flex-direction:column;align-items:center;justify-content:center;padding-top:30px;gap:8px}
.logo-mark{width:22px;height:22px;background:var(--red)}
.logo-name{font-weight:700;font-size:14px;color:#111;text-align:center;line-height:1.2}

.main-nav{position:absolute;left:0;top:162px;width:1073px;height:46px;background:var(--nav-grey);display:flex;justify-content:center;gap:0}
.main-nav a{font-size:19px;color:var(--red);line-height:46px;padding:0 25px}
.main-nav a.current{color:#111}

.hero{position:absolute;left:0;top:208px;width:1073px;height:280px;background:linear-gradient(90deg,#4a2a1a 0%,#8a1d1a 30%,#c9c2b8 50%,#6b3a20 75%,#2a1810 100%)}
.dots{position:absolute;left:0;top:498px;width:1073px;display:flex;justify-content:center;gap:10px}
.dots i{width:9px;height:9px;border-radius:50%;background:#333}
.dots i.on{background:var(--red)}

.welcome{position:absolute;left:80px;top:530px;width:588px}
.welcome h1{font-weight:400;font-size:26px;color:#333;text-align:center;margin-left:-20px}
.divider{position:relative;height:44px;margin-top:2px}
.divider .rule{position:absolute;top:21px;height:3px;border-top:2px solid var(--red);border-bottom:1px solid var(--red)}
.divider .rule.l{left:2px;width:253px}.divider .rule.r{left:313px;width:253px}
.divider .home{position:absolute;left:263px;top:0;width:42px;height:42px;border-radius:50%;background:var(--red);display:flex;align-items:center;justify-content:center}
.welcome p{font-size:13px;line-height:20.5px;color:#444;margin-top:6px}
.welcome p+p{margin-top:20px}
.read-more{position:absolute;left:476px;top:252px;width:112px;height:40px;background:var(--red);color:var(--white);font-weight:700;font-size:14px;display:flex;align-items:center;justify-content:center}

.hours{position:absolute;left:695px;top:536px;width:299px;height:280px;background:var(--wood);padding:9px}
.hours-board{width:100%;height:100%;background:var(--board);border:2px solid #ddd;color:var(--chalk);padding:10px 9px}
.hours h2{font-weight:400;font-size:26px;color:var(--white);text-align:center}
.hours .open{font-size:20px;margin-top:12px}
.hours h3{font-weight:700;font-size:16px;color:var(--white);margin-top:20px}
.hours p{font-size:15px;line-height:21px}

.wine-band{position:absolute;left:0;top:863px;width:1073px;height:232px;background:var(--red-band)}
.ribbon{position:absolute;left:69px;top:857px;width:144px;height:185px}
.ribbon-label{position:absolute;left:69px;top:905px;width:144px;text-align:center;font-family:"Lora",Georgia,serif;font-size:32px;color:var(--white)}
.ribbon-rule{position:absolute;left:92px;top:948px;width:98px;border-top:3px double var(--white)}
.wine-col{position:absolute;top:890px}
.wine-col h4{font-weight:400;font-size:20px;color:#111;margin-bottom:8px}
.wine-col a{display:block;font-weight:700;font-size:15.5px;color:var(--chalk)}
.wine-col.w a,.wine-col.x a{line-height:28px}
.wine-col.r a{line-height:25px}

.footer{position:absolute;left:0;top:1096px;width:1073px;height:104px;background:var(--dark);border-top:2px solid #555}
.footer-nav{position:absolute;left:0;top:22px;width:1073px;display:flex;justify-content:center}
.footer-nav a{font-size:15px;color:var(--white);padding:0 29px}
.footer-nav a.current{color:var(--red)}
.copyright{position:absolute;left:0;top:59px;width:1073px;text-align:center;font-size:13px;color:var(--white)}
.copyright b{color:var(--red);font-weight:400}
</style>
</head>
<body>

<div class="top-bar">
  <div class="reservation">
    <svg width="18" height="18" viewBox="0 0 24 24"><path fill="#fff" d="M6.6 10.8c1.4 2.8 3.8 5.1 6.6 6.6l2.2-2.2c.3-.3.7-.4 1-.2 1.1.4 2.3.6 3.6.6.6 0 1 .4 1 1V20c0 .6-.4 1-1 1C10.6 21 3 13.4 3 4c0-.6.4-1 1-1h3.5c.6 0 1 .4 1 1 0 1.3.2 2.5.6 3.6.1.3 0 .7-.2 1z"/></svg>
    Make a Reservation : +44 100 200 3000
  </div>
  <div class="social">
    <span aria-label="Social profile 1"></span>
    <span aria-label="Social profile 2"></span>
    <span aria-label="Social profile 3"></span>
    <span aria-label="Social profile 4"></span>
    <span aria-label="Email"><svg width="20" height="15" viewBox="0 0 20 15"><rect width="20" height="15" rx="2" fill="#e8171b"/><path d="M1 2l9 6 9-6" stroke="#fff" stroke-width="2" fill="none"/></svg></span>
  </div>
</div>

<div class="header">
  <div class="ornament left" role="img" aria-label="Orange floral scroll ornament"></div>
  <div class="ornament right" role="img" aria-label="Orange floral scroll ornament"></div>
</div>
<div class="logo-arch">
  <span class="logo-mark"></span>
  <span class="logo-name">Chef Wen<br>Chinese Restaurant</span>
</div>

<nav class="main-nav">
  <a class="current">Home</a><a>About</a><a>Menu</a><a>Winelist</a><a>Facilities</a><a>Events</a><a>Contact</a>
</nav>

<div class="hero" role="img" aria-label="Photo of a set dining table with wine glasses, salad and whisky being poured"></div>
<div class="dots"><i class="on"></i><i></i><i></i><i></i></div>

<section class="welcome">
  <h1>Welcome to&nbsp; Chef Wen</h1>
  <div class="divider">
    <span class="rule l"></span>
    <span class="home"><svg width="24" height="22" viewBox="0 0 24 22"><path fill="#fff" d="M12 1L1 11h3v10h6v-6h4v6h6V11h3z"/></svg></span>
    <span class="rule r"></span>
  </div>
  <p>Chef Wen is named after its’ executive chef, Mr. Wen. Chef Wen has been in his career for nearly two decades before he moved to Australia nine years ago. He settled in Adelaide then started his first restaurant, Larkspur Court in Eastwood. Larkspur Court has been running successfully for years due to Chef Wen’s talent of cooking.</p>
  <p>We offer an exceptional dining experience with authentic and dynamic dishes created with quality ingredients. The menu of Chef Wen is based on classic Cantonese dishes, featured by southern China’s local flavour characteristics. Taking advantage of South Australia’s rich and quality food resources...</p>
  <a class="read-more">READ MORE</a>
</section>

<aside class="hours">
  <div class="hours-board">
    <h2>Opening Hours</h2>
    <p class="open">We are open 7 days</p>
    <h3>Lunch :</h3>
    <p>Monday to Friday 11:30am – 2:30pm<br>Saturday to Sunday 11:00am – 3:00pm</p>
    <h3>Dinner :</h3>
    <p>Monday to Sunday 6:00pm Until Late</p>
  </div>
</aside>

<div class="wine-band"></div>
<svg class="ribbon" viewBox="0 0 144 185"><path d="M0 0h144v185l-72-22-72 22z" fill="#333"/><path d="M6 0v170M138 0v170" stroke="#555" stroke-width="4"/></svg>
<div class="ribbon-label">Wines</div>
<div class="ribbon-rule"></div>

<div class="wine-col w" style="left:288px">
  <h4>WINES</h4>
  <a>Champagne</a><a>Sparkling White</a><a>Sparkling Red</a>
</div>
<div class="wine-col x" style="left:493px">
  <h4>WHITE WINE</h4>
  <a>Riesling</a><a>Pinot Gris / Pinot Grigio</a><a>Sauvignon Blanc and Blends</a><a>Chardonnay</a><a>Other White Varietals</a>
</div>
<div class="wine-col r" style="left:726px">
  <h4>RED WINE</h4>
  <a>Rosé</a><a>Pinot Noir</a><a>Grenache/Sangiovese/Merlot</a><a>Cabernet Sauvignon &amp; Blends</a><a>Shiraz and Blends</a><a>Other Red Varietals</a>
</div>

<footer class="footer">
  <nav class="footer-nav">
    <a class="current">Home</a><a>About</a><a>Menu</a><a>Winelist</a><a>Facilities</a><a>Events</a><a>Contact</a>
  </nav>
  <p class="copyright">© <b>Chef Wen</b> - 2014. All Rights Reserved.</p>
</footer>

</body>
</html>
```